RW Framewell Inc Business cards

We need business cards using our existing logo but slightly modified. Right now the logo says RW Loadbearing Masonry. We want to keep the RW part of the design, but replace the Structural Concrete portion with "FRAMEWELL". Please see the attached file.
Ideally this would be a blank template so we can add Different Names, titles, and phone numbers later.
On the one side we want only the logo and on the other side the detail. I'm attaching an example for you to see.
Please reach out with any other questions. Our address and other details will be given out once we find a design we like.

Target Market(s)

Construction Industry

```html
<!DOCTYPE html>
<html lang="en">
<head>
<meta charset="utf-8">
<title>RW Framewell Inc – Business Cards</title>
<link rel="stylesheet" href="https://fonts.googleapis.com/css2?family=Archivo+Black&family=Arimo:wght@400&display=swap">
<style>
  :root {
    --stage: #1c1c1c;
    --kraft-light: #dcbb8e;
    --kraft-mid: #c39a68;
    --kraft-dark: #a97b4c;
    --ink: #0c0a08;
    --rule: #7a5a38;
  }
  * { box-sizing: border-box; margin: 0; padding: 0; }
  html, body { width: 1093px; height: 1200px; overflow: hidden; }
  body { background: var(--stage); position: relative; }

  .card {
    position: absolute;
    left: 264px;
    width: 580px;
    height: 357px;
    background: linear-gradient(155deg, var(--kraft-light) 0%, var(--kraft-mid) 55%, var(--kraft-dark) 100%);
    color: var(--ink);
    text-align: center;
  }
  .card--front { top: 226px; }
  .card--back { top: 620px; }

  .holder-name {
    position: absolute; top: 83px; left: 0; right: 0;
    font: 27px/1 "Archivo Black", sans-serif;
    letter-spacing: 0.5px;
  }
  .holder-title {
    position: absolute; top: 114px; left: 0; right: 0;
    font: 21px/1 "Arimo", sans-serif;
  }
  .contact-icons {
    position: absolute; top: 153px; left: 0; right: 0;
    display: flex; justify-content: center; align-items: center; gap: 5px;
  }
  .contact-icons .rule { width: 64px; height: 1px; background: var(--rule); margin: 0 6px; }
  .contact-icons svg { width: 31px; height: 31px; display: block; }
  .contact-list {
    position: absolute; top: 199px; left: 0; right: 0;
    list-style: none;
    font: 21px/27px "Arimo", sans-serif;
  }

  .brand {
    position: absolute; top: 100px; left: 0; right: 0;
    font-family: "Archivo Black", sans-serif;
    line-height: 1;
  }
  .brand-initials { display: block; font-size: 126px; letter-spacing: 4px; }
  .brand-word { display: block; font-size: 40px; letter-spacing: 1px; margin-top: 4px; }
</style>
</head>
<body>
  <section class="card card--front" aria-label="Card front – contact details">
    <h1 class="holder-name">DANIEL HARROW</h1>
    <p class="holder-title">Managing Director</p>
    <div class="contact-icons">
      <span class="rule"></span>
      <svg viewBox="0 0 32 32" aria-label="Phone"><rect width="32" height="32" rx="4" fill="#0c0a08"/><path d="M7 13c0-3 4-4 9-4s9 1 9 4v1h-4v-2h-10v2H7z M10 15h12l2 8H8z" fill="#dcbb8e"/></svg>
      <svg viewBox="0 0 32 32" aria-label="Email"><rect width="32" height="32" rx="4" fill="#0c0a08"/><rect x="7" y="10" width="18" height="12" fill="none" stroke="#dcbb8e" stroke-width="1.5"/><path d="M7 10l9 7 9-7M7 22l7-6M25 22l-7-6" fill="none" stroke="#dcbb8e" stroke-width="1.2"/></svg>
      <svg viewBox="0 0 32 32" aria-label="Website"><rect width="32" height="32" rx="4" fill="#0c0a08"/><circle cx="16" cy="16" r="9" fill="#dcbb8e"/><path d="M16 7v18M7 16h18M16 7c-5 4-5 14 0 18M16 7c5 4 5 14 0 18" fill="none" stroke="#0c0a08" stroke-width="1"/></svg>
      <span class="rule"></span>
    </div>
    <ul class="contact-list">
      <li>044-987 654 321</li>
      <li>info@rwframewell.com</li>
      <li>www.rwframewell.com</li>
    </ul>
  </section>

  <section class="card card--back" aria-label="Card back – company name">
    <p class="brand">
      <span class="brand-initials">RW</span>
      <span class="brand-word">FRAMEWELL</span>
    </p>
  </section>
</body>
</html>
```